Fitness website

Website for a fitness brand (see attached specs). Design needs to be modern and vibrant with CTAs on every page. We will provide logos, images, etc but for now user placeholder text and images. For now use the name 'Corvane Athletics' as the name to use on the design. The goal of this site is to either get people to join the gym (5 physical locations across the US); buy an online program; buy merch or supplements or sign up for the newsletter. Pleas use images from this foldeR: https://filebarn.example/share/folders/8QwTz41mKpLrXv93NdYe7HsaBuJ0Cf2_R?usp=sharing

We will be coding this in ReactNative. Lots more work for the winner as well, this is a 1st project for us.

Target Market(s)

fitness enthusiats

Industry/Entity Type

fitness, health, wellness

Number of Pages Required

5+ page

Font styles to use
Other font styles liked:
• Lato

Colors
0054AA
0677BA
7BADD7
CADEEF
E8F1F8
0094D4
00A9DD
6FCCEA
C7EBF8
E9F6FB
00AB8E
00BBA5
67D7C9
C6EFE9
E9F9F6
EE7325
F08F49
F5BC92
FAE3D3
FDF4ED

Requirements
Must have
• must be reactive. most people will view it first on mobile
Nice to have
• video in hero section of top of home page

```html
<!DOCTYPE html>
<html lang="en">
<head>
<meta charset="utf-8">
<title>Corvane Athletics — Strength. Mindset. Results</title>
<link href="https://fonts.googleapis.com/css2?family=Lato:wght@400;700;900&family=Poppins:wght@400;500&display=swap" rel="stylesheet">
<style>
:root{
  --navy:#1b3d9c;
  --teal:#1f9d86;
  --teal-light:#2bb39a;
  --green:#1e8a70;
  --ink:#111;
  --text:#333;
  --muted:#8a8a8a;
  --white:#fff;
  --grey-map:#a3a3a3;
  --grey-map-dark:#8e8e8e;
  --red:#d81e3a;
  --star:#f5a623;
  --black:#000;
}
*{margin:0;padding:0;box-sizing:border-box}
html,body{width:1200px;height:4532px;overflow:hidden}
body{font-family:'Lato',sans-serif;color:var(--text);background:var(--white);position:relative}
.abs{position:absolute}
a{color:inherit;text-decoration:none}

/* Hero */
.hero{position:absolute;left:0;top:0;width:1200px;height:800px;overflow:hidden}
.hero-photo{position:absolute;inset:0;background:linear-gradient(180deg,#1c2733 0%,#2a3846 45%,#33404c 100%)}
.hero-shade{position:absolute;inset:0;background:radial-gradient(ellipse at 50% 35%,rgba(40,60,90,.35),rgba(10,15,25,.55))}
.nav{position:absolute;top:36px;left:90px;right:90px;height:40px;display:flex;align-items:center}
.brand{font-weight:900;font-size:30px;color:var(--white);letter-spacing:.3px}
.menu{display:flex;gap:32px;margin-left:58px;font-size:14px;color:var(--white)}
.menu .active{color:var(--teal-light)}
.search{margin-left:28px;width:16px;height:16px}
.nav-cta{margin-left:auto;background:var(--navy);color:var(--white);font-size:13px;padding:10px 20px;border-radius:20px}
.hero-title{position:absolute;top:178px;width:100%;text-align:center;font-size:52px;font-weight:900;color:var(--white);letter-spacing:.5px}
.hero-sub{position:absolute;top:258px;left:310px;width:580px;text-align:center;font-size:17px;line-height:31px;color:var(--white)}
.hero-btns{position:absolute;top:344px;width:100%;display:flex;justify-content:center;gap:22px}
.btn-light{background:var(--white);color:var(--ink);font-weight:700;font-size:15px;padding:15px 28px;border-radius:30px}
.btn-ghost{border:2px solid var(--white);color:var(--white);font-weight:700;font-size:15px;padding:13px 26px;border-radius:30px}

.hexes{position:absolute;top:510px;left:0;width:1200px;height:310px}
.hex{position:absolute;text-align:center;color:var(--white)}
.hex svg.shape{position:absolute;inset:0}
.hex .in{position:relative;padding:0 22px}
.hex h3{font-size:19px;font-weight:700;margin-bottom:12px}
.hex p{font-size:13px;line-height:26px}
.hex-icon{width:44px;height:44px;margin:0 auto 14px;display:block}

/* About */
.about-photo{position:absolute;left:0;top:855px;width:540px;height:555px;background:linear-gradient(135deg,#e9e6e2 0%,#c9bfb4 50%,#5a4e46 100%);clip-path:polygon(0 0,100% 0,100% 45%,80% 100%,0 100%)}
.about{position:absolute;left:598px;top:915px;width:490px}
.h2{font-size:34px;font-weight:900;color:var(--ink)}
.h2 .accent{color:var(--navy)}
.about p{font-size:13.5px;line-height:26px;color:var(--text);margin-top:10px}
.about p+p{margin-top:26px}
.btn-grad{display:inline-block;background:linear-gradient(90deg,var(--navy) 0%,var(--teal) 100%);color:var(--white);font-weight:700;font-size:15px;padding:15px 30px;border-radius:28px;box-shadow:0 4px 8px rgba(0,0,0,.25)}
.about .btn-grad{margin-top:24px}

/* Programs */
.programs-bg{position:absolute;left:0;top:1411px;width:1200px;height:430px}
.prog-head{position:absolute;top:1468px;width:100%;text-align:center;color:var(--white)}
.prog-head h2{font-size:34px;font-weight:900}
.prog-head p{width:770px;margin:18px auto 0;font-size:14px;line-height:30px}
.card{position:absolute;top:1624px;width:313px;height:335px}
.card .img{position:absolute;left:0;top:0;width:313px;height:256px}
.card .box{position:absolute;left:20px;top:198px;width:273px;height:137px;background:var(--white);padding:20px 20px;box-shadow:0 4px 12px rgba(0,0,0,.12)}
.card h4{font-size:16px;font-weight:700;color:var(--ink)}
.card p{font-size:13.5px;line-height:23px;color:var(--muted);margin-top:8px}
.card a{display:block;margin-top:8px;font-size:12.5px;font-weight:700;color:var(--teal);text-decoration:underline}
.view-more{position:absolute;top:2022px;left:522px}

/* Locations */
.loc-head{position:absolute;top:2140px;width:100%;text-align:center}
.loc-head p{width:830px;margin:18px auto 0;font-size:14px;line-height:30px}
.map{position:absolute;left:170px;top:2288px;width:860px;height:546px;border-radius:16px;background:linear-gradient(160deg,var(--grey-map) 0%,var(--grey-map-dark) 100%)}
.pin{position:absolute;width:34px;height:46px}
.callout{position:absolute;left:296px;top:2536px;width:104px;height:70px;background:var(--teal);border:2px solid var(--white);border-radius:10px;color:var(--white);text-align:center;font-size:16px;line-height:22px;padding-top:11px}

/* Gear */
.gear{position:absolute;left:0;top:2913px;width:1200px;height:463px;background:var(--green);overflow:hidden}
.gear-photo{position:absolute;right:0;top:0;width:610px;height:463px;background:linear-gradient(135deg,#2a2f36 0%,#4a4540 55%,#1b1e22 100%);clip-path:polygon(18% 0,100% 0,100% 100%,15% 100%,0 50%)}
.gear-text{position:absolute;left:111px;top:60px;width:460px;color:var(--white)}
.gear-text h2{font-size:34px;font-weight:900}
.gear-text p{font-size:13.5px;line-height:26px;margin-top:10px}
.gear-text p+p{margin-top:26px}
.btn-white{display:inline-block;margin-top:22px;background:var(--white);color:var(--teal);font-weight:700;font-size:15px;padding:15px 28px;border-radius:30px}

/* Testimonials */
.test-head{position:absolute;top:3452px;width:100%;text-align:center}
.tcard{position:absolute;width:312px;background:var(--white);border:1px solid #e3e3e3;box-shadow:0 2px 10px rgba(0,0,0,.08);padding:30px 16px 0}
.stars{color:var(--star);font-size:18px;letter-spacing:2px}
.tcard p{font-family:'Poppins',sans-serif;font-size:15px;line-height:27px;color:#222;margin-top:16px}
.person{display:flex;align-items:center;margin-top:20px}
.avatar{width:64px;height:64px;border-radius:50%;background:linear-gradient(135deg,#c9b8a8,#6e5a4c);margin-right:16px;flex:none}
.person b{font-family:'Poppins',sans-serif;font-weight:500;font-size:15px;color:#111;display:block}
.person span{font-size:13px;color:var(--muted)}

/* Footer */
.footer-bg{position:absolute;left:0;top:3960px;width:1200px;height:572px}
.footer{position:absolute;left:0;top:4160px;width:1200px;color:var(--white)}
.fcol{position:absolute;top:0}
.fcol h5{font-size:22px;font-weight:400;letter-spacing:.3px}
.fcol ul{list-style:none;margin-top:20px}
.fcol li{font-size:14px;line-height:34.5px;display:flex;align-items:center}
.fcol li svg{margin-right:12px}
.socials{display:flex;gap:18px;margin-top:20px}
.social{width:28px;height:28px;border-radius:50%;border:2px solid var(--white)}
.social.on{background:var(--teal);border-color:var(--teal)}
.contact-row{display:flex;align-items:flex-start;font-size:14px;line-height:26px;margin-top:16px}
.contact-row .ic{width:30px;height:30px;border-radius:50%;background:var(--white);margin-right:14px;flex:none;display:flex;align-items:center;justify-content:center}
.footer-rule{position:absolute;left:111px;top:4415px;width:978px;height:1px;background:#333}
.copyright{position:absolute;top:4463px;width:100%;text-align:center;font-size:14px;color:var(--white)}
</style>
</head>
<body>

<!-- Hero -->
<section class="hero">
  <div class="hero-photo" role="img" aria-label="Athletes training hard with barbells in a gym"></div>
  <div class="hero-shade"></div>
  <nav class="nav">
    <div class="brand">CORVANE ATHLETICS</div>
    <div class="menu">
      <a class="active">HOME</a><a>About</a><a>Program</a><a>Blog</a><a>Members</a><a>Affiliates</a>
    </div>
    <svg class="search" viewBox="0 0 16 16"><circle cx="6.5" cy="6.5" r="5" fill="none" stroke="#fff" stroke-width="1.6"/><line x1="10.5" y1="10.5" x2="15" y2="15" stroke="#fff" stroke-width="1.6"/></svg>
    <a class="nav-cta">CONTACT US</a>
  </nav>
  <h1 class="hero-title">STRENGTH. MINDSET. RESULTS</h1>
  <p class="hero-sub">Push your limits with Corvane Athletics — where elite coaching meets unstoppable community.</p>
  <div class="hero-btns"><a class="btn-light">JOIN A GYM</a><a class="btn-ghost">START ONLINE TRAINING</a></div>
  <svg class="abs" style="left:0;top:560px" width="1200" height="240" viewBox="0 0 1200 240" preserveAspectRatio="none">
    <path d="M0 210 C260 90 620 170 900 110 C1040 80 1140 40 1200 20 L1200 240 L0 240 Z" fill="var(--teal)"/>
    <path d="M0 240 C280 120 640 200 920 140 C1050 110 1150 70 1200 50 L1200 240 Z" fill="#fff"/>
  </svg>
</section>

<!-- Feature hexagons -->
<div class="hexes">
  <div class="hex" style="left:142px;top:4px;width:268px;height:300px">
    <svg class="shape" viewBox="0 0 268 300"><path d="M134 4 L254 68 Q264 74 264 86 L264 214 Q264 226 254 232 L134 296 L14 232 Q4 226 4 214 L4 86 Q4 74 14 68 Z" fill="var(--navy)"/></svg>
    <div class="in" style="padding-top:46px">
      <svg class="hex-icon" viewBox="0 0 44 44"><circle cx="22" cy="16" r="8" fill="none" stroke="#fff" stroke-width="2.5"/><path d="M10 40 Q22 26 34 40" fill="none" stroke="#fff" stroke-width="2.5"/></svg>
      <h3>Elite Coaching</h3>
      <p>Excepteur sint occaecat cupidatat non proident, sunt in culpa qui eserunt mollit anim id est laborum.</p>
    </div>
  </div>
  <div class="hex" style="left:442px;top:-20px;width:306px;height:330px">
    <svg class="shape" viewBox="0 0 306 330"><defs><linearGradient id="hexg" x1="0" y1="0" x2="0" y2="1"><stop offset="0" stop-color="var(--navy)"/><stop offset="1" stop-color="var(--teal-light)"/></linearGradient></defs><path d="M153 4 L290 74 Q302 80 302 94 L302 236 Q302 250 290 256 L153 326 L16 256 Q4 250 4 236 L4 94 Q4 80 16 74 Z" fill="url(#hexg)"/></svg>
    <div class="in" style="padding-top:36px">
      <svg class="hex-icon" viewBox="0 0 44 44"><circle cx="22" cy="14" r="9" fill="none" stroke="#fff" stroke-width="2.5"/><path d="M6 24 Q12 38 22 38 Q32 38 38 24" fill="none" stroke="#fff" stroke-width="2.5"/></svg>
      <h3 style="font-size:22px">Smart Programs</h3>
      <p style="font-size:15px;line-height:32px">Excepteur sint occaecat cupidatat non proident, sunt in culpa qui eserunt mollit anim id est laborum.</p>
    </div>
  </div>
  <div class="hex" style="left:780px;top:4px;width:268px;height:300px">
    <svg class="shape" viewBox="0 0 268 300"><path d="M134 4 L254 68 Q264 74 264 86 L264 214 Q264 226 254 232 L134 296 L14 232 Q4 226 4 214 L4 86 Q4 74 14 68 Z" fill="var(--navy)"/></svg>
    <div class="in" style="padding-top:46px">
      <svg class="hex-icon" viewBox="0 0 44 44"><circle cx="22" cy="22" r="19" fill="none" stroke="#fff" stroke-width="2.5"/><circle cx="22" cy="16" r="5" fill="#fff"/><circle cx="12" cy="22" r="4" fill="#fff"/><circle cx="32" cy="22" r="4" fill="#fff"/><path d="M12 34 Q22 22 32 34" fill="#fff"/></svg>
      <h3>Strong Community</h3>
      <p>Excepteur sint occaecat cupidatat non proident, sunt in culpa qui eserunt mollit anim id est laborum.</p>
    </div>
  </div>
</div>

<!-- About -->
<div class="about-photo" role="img" aria-label="Two athletes lifting dumbbells"></div>
<section class="about">
  <h2 class="h2">ABOUT <span class="accent">CORVANE ATHLETICS</span></h2>
  <p>Corvane Athletics was founded on one simple belief: everyone has the power to become unconquered. We combine elite-level coaching, proven training systems, and a community that holds you accountable — both in person and online. Whether you're stepping into one of our five U.S. locations or training from home, you'll experience a culture built around growth, grit, and lasting results.</p>
  <p>Every program we create is designed to help athletes — from beginners to pros — move, perform, and live at their highest potential. Excepteur sint occaecat cupidatat non proident, sunt in culpa qui officia deserunt mollit anim id est laborum.</p>
  <a class="btn-grad">READ MORE</a>
</section>

<!-- Online program -->
<svg class="programs-bg" viewBox="0 0 1200 430" preserveAspectRatio="none">
  <path d="M0 0 H1200 V240 C1080 300 1000 250 900 300 L300 300 C180 330 80 360 0 420 Z" fill="var(--navy)"/>
</svg>
<div class="prog-head">
  <h2>OUR ONLINE PROGRAM</h2>
  <p>Duis aute irure dolor in reprehenderit in voluptate velit esse cillum dolore eu fugiat nulla pariatur. Excepteur sint occaecat cupidatat non proident, sunt in culpa qui officia deserunt mollit anim id est laborum.</p>
</div>
<div class="card" style="left:111px">
  <div class="img" role="img" aria-label="Athletes lifting barbells overhead" style="background:linear-gradient(160deg,#3c4450,#1f242b)"></div>
  <div class="box"><h4>MASTERS</h4><p>Duis aute irure dolor in reprehend in voluptate velit</p><a>READ MORE</a></div>
</div>
<div class="card" style="left:442px">
  <div class="img" role="img" aria-label="Athlete training with battle ropes" style="background:linear-gradient(160deg,#4a4a4a,#1c1c1c)"></div>
  <div class="box"><h4>FUNCTIONAL FITNESS</h4><p>Duis aute irure dolor in reprehend in voluptate velit</p><a>READ MORE</a></div>
</div>
<div class="card" style="left:774px">
  <div class="img" role="img" aria-label="Athlete resting in the gym" style="background:linear-gradient(160deg,#5a4a3a,#2a2520)"></div>
  <div class="box"><h4>COMPETITIVE</h4><p>Duis aute irure dolor in reprehend in voluptate velit</p><a>READ MORE</a></div>
</div>
<a class="btn-grad view-more">VIEW MORE</a>

<!-- Locations -->
<section class="loc-head">
  <h2 class="h2">TRAIN WITH US — <span class="accent">ACROSS 5 U.S. LOCATIONS</span></h2>
  <p>Duis aute irure dolor in reprehenderit in voluptate velit esse cillum dolore eu fugiat nulla pariatur. Excepteur sint occaecat cupidatat non proident, sunt in culpa qui officia deserunt mollit anim id est laborum.</p>
</section>
<div class="map" role="img" aria-label="Map of the United States with pins marking the five gym locations"></div>
<svg class="pin" style="left:256px;top:2298px" viewBox="0 0 34 46"><path d="M17 45 C8 30 1 24 1 16 A16 16 0 0 1 33 16 C33 24 26 30 17 45 Z" fill="var(--red)" stroke="#fff" stroke-width="2"/><circle cx="17" cy="16" r="6" fill="#fff"/></svg>
<svg class="pin" style="left:262px;top:2620px" viewBox="0 0 34 46"><path d="M17 45 C8 30 1 24 1 16 A16 16 0 0 1 33 16 C33 24 26 30 17 45 Z" fill="var(--red)" stroke="#fff" stroke-width="2"/><circle cx="17" cy="16" r="6" fill="#fff"/></svg>
<svg class="pin" style="left:960px;top:2390px" viewBox="0 0 34 46"><path d="M17 45 C8 30 1 24 1 16 A16 16 0 0 1 33 16 C33 24 26 30 17 45 Z" fill="var(--red)" stroke="#fff" stroke-width="2"/><circle cx="17" cy="16" r="6" fill="#fff"/></svg>
<svg class="pin" style="left:924px;top:2462px" viewBox="0 0 34 46"><path d="M17 45 C8 30 1 24 1 16 A16 16 0 0 1 33 16 C33 24 26 30 17 45 Z" fill="var(--red)" stroke="#fff" stroke-width="2"/><circle cx="17" cy="16" r="6" fill="#fff"/></svg>
<svg class="pin" style="left:913px;top:2728px" viewBox="0 0 34 46"><path d="M17 45 C8 30 1 24 1 16 A16 16 0 0 1 33 16 C33 24 26 30 17 45 Z" fill="var(--red)" stroke="#fff" stroke-width="2"/><circle cx="17" cy="16" r="6" fill="#fff"/></svg>
<div class="callout">San Diego<br>(HQ)</div>

<!-- Gear up -->
<section class="gear">
  <div class="gear-photo" role="img" aria-label="Athlete pushing hard on a bike erg"></div>
  <div class="gear-text">
    <h2>GEAR UP FOR GREATNESS</h2>
    <p>Lorem ipsum dolor sit amet, consectetur adipiscing elit, sed do eiusmod tempor incididunt ut labore et dolore magna aliqua. Ut enim ad minim veniam, quis nostrud exercitation ullamco laboris nisi ut aliquip ex ea commodo consequat.</p>
    <p>Duis aute irure dolor in reprehenderit in voluptate velit esse cillum dolore eu fugiat nulla pariatur. Excepteur sint occaecat reprehen derit in voluptate velit esse cillum cupidatat non proident, sunt in culpa qui officia deserunt mollit anim id est laborum.</p>
    <a class="btn-white">CONTACT US</a>
  </div>
</section>

<!-- Testimonials -->
<section class="test-head"><h2 class="h2">WHAT OUR <span class="accent">CUSTOMER SAYS</span></h2></section>
<div class="tcard" style="left:111px;top:3545px;height:390px">
  <div class="stars">★★★★★</div>
  <p>Temporibus autem quibusdam et aut officiis debitis aut rerum neus saepe facere mus, onis voluptas eveniet ut et voluptates repudae sint et molestiae non lorem recusadae.</p>
  <div class="person"><div class="avatar"></div><div><b>Dorian Haskell</b><span>United States</span></div></div>
</div>
<div class="tcard" style="left:453px;top:3585px;height:390px">
  <div class="stars">★★★★★</div>
  <p>Itaque earum rerum hic tenetur a sapiene delectus, ut aut reiciels volupatibus maiores alias conse uatur aut perferndis doloribus asperiores reiciendis voluptatbus repellat</p>
  <div class="person"><div class="avatar"></div><div><b>Selina</b><span>United States</span></div></div>
</div>
<div class="tcard" style="left:793px;top:3545px;height:390px">
  <div class="stars">★★★★★</div>
  <p>At vero eos et accusamus et iusto odio dignissimos ducimus qui blaiis praesentium volupttum deleniti atque corrupti quos dolores et quas occaecati cupie non provident</p>
  <div class="person"><div class="avatar"></div><div><b>Marco Bellin</b><span>United States</span></div></div>
</div>
<div class="tcard" style="left:1141px;top:3585px;height:350px">
  <div class="stars">★★</div>
</div>

<!-- Footer -->
<svg class="footer-bg" viewBox="0 0 1200 572" preserveAspectRatio="none">
  <path d="M0 150 C200 60 420 100 620 110 C850 120 1050 60 1200 0 V80 C1050 140 850 170 620 150 C420 140 200 130 0 200 Z" fill="var(--navy)"/>
  <path d="M0 200 C200 130 420 140 620 150 C850 170 1050 140 1200 80 V572 H0 Z" fill="var(--black)"/>
</svg>
<footer class="footer">
  <div class="fcol" style="left:111px">
    <h5 style="font-weight:700;font-size:26px">CORVANE ATHLETICS</h5>
    <div class="socials"><span class="social on"></span><span class="social"></span><span class="social"></span><span class="social"></span></div>
  </div>
  <div class="fcol" style="left:430px">
    <h5>QUICK LINKS</h5>
    <ul>
      <li><svg width="12" height="12" viewBox="0 0 12 12"><path d="M0 5h8V1l4 5-4 5V7H0z" fill="#fff"/></svg>Home</li>
      <li><svg width="12" height="12" viewBox="0 0 12 12"><path d="M0 5h8V1l4 5-4 5V7H0z" fill="#fff"/></svg>About</li>
      <li><svg width="12" height="12" viewBox="0 0 12 12"><path d="M0 5h8V1l4 5-4 5V7H0z" fill="#fff"/></svg>Program</li>
      <li><svg width="12" height="12" viewBox="0 0 12 12"><path d="M0 5h8V1l4 5-4 5V7H0z" fill="#fff"/></svg>Testimonials</li>
      <li><svg width="12" height="12" viewBox="0 0 12 12"><path d="M0 5h8V1l4 5-4 5V7H0z" fill="#fff"/></svg>Contact Us</li>
    </ul>
  </div>
  <div class="fcol" style="left:662px">
    <h5>HELP LINKS</h5>
    <ul>
      <li><svg width="12" height="12" viewBox="0 0 12 12"><path d="M0 5h8V1l4 5-4 5V7H0z" fill="#fff"/></svg>FAQ</li>
      <li><svg width="12" height="12" viewBox="0 0 12 12"><path d="M0 5h8V1l4 5-4 5V7H0z" fill="#fff"/></svg>Shop</li>
      <li><svg width="12" height="12" viewBox="0 0 12 12"><path d="M0 5h8V1l4 5-4 5V7H0z" fill="#fff"/></svg>Privacy Policy</li>
      <li><svg width="12" height="12" viewBox="0 0 12 12"><path d="M0 5h8V1l4 5-4 5V7H0z" fill="#fff"/></svg>Affiliates</li>
      <li><svg width="12" height="12" viewBox="0 0 12 12"><path d="M0 5h8V1l4 5-4 5V7H0z" fill="#fff"/></svg>Members</li>
    </ul>
  </div>
  <div class="fcol" style="left:867px;width:240px">
    <h5 style="font-weight:700">CONTACT US</h5>
    <div class="contact-row" style="margin-top:20px"><span class="ic"><svg width="14" height="18" viewBox="0 0 14 18"><path d="M7 17C3 11 1 9 1 6.5A6 6 0 0 1 13 6.5C13 9 11 11 7 17Z" fill="#000"/><circle cx="7" cy="6.5" r="2.2" fill="#fff"/></svg></span><span>Corvane Athletics<br>United States</span></div>
    <div class="contact-row"><span class="ic"><svg width="16" height="16" viewBox="0 0 16 16"><path d="M3 1l3 3-1.5 2a9 9 0 0 0 5.5 5.5L12 10l3 3-2 2C7 15 1 9 1 3z" fill="#000"/></svg></span><span style="line-height:30px">+1 555 014 2290</span></div>
    <div class="contact-row"><span class="ic"><svg width="16" height="12" viewBox="0 0 16 12"><rect width="16" height="12" rx="1.5" fill="#000"/><path d="M1 1l7 6 7-6" fill="none" stroke="#fff" stroke-width="1.4"/></svg></span><span style="line-height:30px">info@corvaneathletics.example</span></div>
  </div>
</footer>
<div class="footer-rule"></div>
<p class="copyright">Copyrights@2025.Corvane Athletics.All Rights Reserved</p>

</body>
</html>
```